Business Cards for new orthopaedic surgery practice

My husband and I are starting our own orthopaedic surgery practice. We are looking for a business card that is uniform, but one will have my name/title and the other will have his. You can just create one design with my name on it for now. But when I choose your design as the winning design I will ask that you add another copy with his name/title.

We are looking for classy, simple, elite all in one. We like dark blues/a little gold/yellow. Something that goes with our logo. We want our logo incorporated. Here is all the info you need:
Business name: RV Bone & Vitality Center
Location: 38517 North Willowmere Ave
Maple Harbor, FL 33482
Phone: 954-218-4063
Fax: 954-582-7341
Email: info@myrvbonecare.example

Names: Lydia Vance, M.D.
Board Certified Hand and Upper Extremity Surgeon

Ebo Dansu, M.D.
Board Certified Hip & Knee Replacement/General Orthopaedic Surgeon

Can decide what you want to put on the back. Maybe a slogan:
Grounded in Care. Centered on You

I am just going to upload our logo. The only thing is if we select you as the winning design, the location, and phone numbers may change. We will need your help to update that once fully solidified.

Industry/Entity Type

Medical

Contact Information for Business Card

Colors
0054AA
0677BA
7BADD7
CADEEF
E8F1F8
0094D4
00A9DD
6FCCEA
C7EBF8
E9F6FB

Requirements
Must have
• class, appeal,
Should not have
• We want to air on the side of masculine if we are looking at masculine vs. feminine feel. But we still want it classy, sophisticated, and something we will love

```html
<!DOCTYPE html>
<html lang="en">
<head>
<meta charset="utf-8">
<title>RV Bone &amp; Vitality Center – Business Cards</title>
<link href="https://fonts.googleapis.com/css2?family=Cinzel:wght@500;600&family=Montserrat:wght@400;500;600&display=swap" rel="stylesheet">
<style>
  :root {
    --backdrop: #c4c4c4;
    --navy: #1b2a52;
    --gold: #c9a35a;
    --white: #ffffff;
    --shadow: rgba(0, 0, 0, 0.28);
  }
  * { box-sizing: border-box; margin: 0; padding: 0; }
  html, body {
    width: 1200px; height: 802px; overflow: hidden;
    background: var(--backdrop);
  }
  .canvas {
    width: 1200px; height: 802px;
    display: flex; align-items: center; justify-content: center; gap: 48px;
  }
  .card {
    position: relative;
    width: 540px; height: 309px;
    background: var(--navy);
    border-radius: 22px;
    overflow: hidden;
    box-shadow: 0 14px 30px var(--shadow);
    color: var(--white);
  }

  /* Front */
  .edge-band {
    position: absolute; top: 0; right: 0; width: 14px; height: 100%;
    background: linear-gradient(to bottom, var(--white) 0 62%, var(--gold) 62% 100%);
  }
  .gold-tab {
    position: absolute; top: 18px; right: 14px; width: 24px; height: 32px;
    background: var(--gold);
  }
  .doctor {
    position: absolute; top: 24px; right: 48px; text-align: right;
  }
  .doctor-name {
    font-family: "Cinzel", serif; font-weight: 600; font-size: 19px;
    color: var(--gold); letter-spacing: 0.5px;
  }
  .doctor-title {
    font-family: "Montserrat", sans-serif; font-size: 11.5px; line-height: 1.35;
    margin-top: 4px;
  }
  .brand {
    position: absolute; left: 32px; top: 112px;
    display: flex; align-items: center; gap: 12px;
  }
  .brand-dot {
    width: 14px; height: 14px; border-radius: 50%; background: var(--gold);
  }
  .brand-name {
    font-family: "Cinzel", serif; font-weight: 500; font-size: 15px;
    line-height: 1.35; letter-spacing: 1.5px; color: var(--white);
  }
  .contact {
    position: absolute; left: 32px; bottom: 28px;
    font-family: "Montserrat", sans-serif; font-size: 11.5px; line-height: 1.55;
    list-style: none;
  }
  .contact li { display: flex; align-items: center; gap: 8px; }
  .contact svg { width: 11px; height: 11px; flex: none; }
  .contact .no-icon { padding-left: 19px; }

  /* Back */
  .card-back {
    display: flex; flex-direction: column; align-items: center; justify-content: center;
    gap: 30px;
  }
  .back-brand {
    display: flex; flex-direction: column; align-items: center; gap: 14px;
  }
  .back-dot {
    width: 22px; height: 22px; border-radius: 50%; background: var(--gold);
  }
  .back-name {
    font-family: "Cinzel", serif; font-weight: 500; font-size: 22px;
    letter-spacing: 2.5px; text-align: center; line-height: 1.4;
  }
  .slogan {
    font-family: "Montserrat", sans-serif; font-weight: 600; font-size: 15px;
    color: var(--gold); letter-spacing: 0.3px;
  }
</style>
</head>
<body>
<main class="canvas">

  <section class="card card-front" aria-label="Business card front">
    <div class="edge-band"></div>
    <div class="gold-tab"></div>

    <div class="doctor">
      <p class="doctor-name">LYDIA VANCE, M.D.</p>
      <p class="doctor-title">Board Certified Hand and Upper<br>Extremity Surgeon</p>
    </div>

    <div class="brand">
      <span class="brand-dot"></span>
      <p class="brand-name">RV Bone &amp;<br>Vitality Center</p>
    </div>

    <ul class="contact">
      <li class="no-icon">38517 North Willowmere Ave</li>
      <li class="no-icon">Maple Harbor, FL 33482</li>
      <li>
        <svg viewBox="0 0 24 24" aria-hidden="true"><path fill="#c9a35a" d="M6.6 10.8a15.1 15.1 0 0 0 6.6 6.6l2.2-2.2c.3-.3.7-.4 1-.2 1.1.4 2.3.6 3.6.6.6 0 1 .4 1 1V20c0 .6-.4 1-1 1C10.6 21 3 13.4 3 4c0-.6.4-1 1-1h3.5c.6 0 1 .4 1 1 0 1.3.2 2.5.6 3.6.1.3 0 .7-.2 1z"/></svg>
        954-218-4063
      </li>
      <li>
        <svg viewBox="0 0 24 24" aria-hidden="true"><path fill="#c9a35a" d="M6 3h10v5H6zM4 9h16a2 2 0 0 1 2 2v6h-4v4H6v-4H2v-6a2 2 0 0 1 2-2zm4 7v3h8v-3z"/></svg>
        954-582-7341
      </li>
      <li>
        <svg viewBox="0 0 24 24" aria-hidden="true"><path fill="#c9a35a" d="M2 5h20v14H2zm2 2v.5l8 5 8-5V7z"/></svg>
        info@myrvbonecare.example
      </li>
    </ul>
  </section>

  <section class="card card-back" aria-label="Business card back">
    <div class="back-brand">
      <span class="back-dot"></span>
      <p class="back-name">RV BONE &amp;<br>VITALITY CENTER</p>
    </div>
    <p class="slogan">Grounded in Care. Centered on You</p>
  </section>

</main>
</body>
</html>
```